Harbor Loom Floors Letterhead

Letterhead used for business reasons. It must be editable and easy to use.

Address is 2715 W. Pelican Lane Englewood FL 34187 - 941.382.6519

```html
<!DOCTYPE html>
<html lang="en">
<head>
<meta charset="utf-8">
<title>Harbor Loom Floors Letterhead</title>
<link href="https://fonts.googleapis.com/css2?family=Lato:wght@400;700&family=Montserrat:wght@400&family=Satisfy&display=swap" rel="stylesheet">
<style>
  :root {
    --backdrop: #e9e9ea;
    --paper: #ffffff;
    --brand-orange: #e38f2a;
    --brand-grey: #948a86;
    --ink: #1d1d1d;
    --ink-soft: #444444;
  }
  html, body {
    margin: 0;
    padding: 0;
    width: 1200px;
    height: 874px;
    overflow: hidden;
    background: var(--backdrop);
  }
  .letterhead {
    position: absolute;
    left: 300px;
    top: 13px;
    width: 600px;
    height: 848px;
    background: var(--paper);
    box-shadow: 0 2px 10px rgba(0,0,0,0.12);
    overflow: hidden;
    font-family: 'Lato', sans-serif;
    color: var(--ink);
  }
  .contact-block {
    position: absolute;
    top: 48px;
    right: 46px;
    padding-left: 14px;
    font-family: 'Montserrat', sans-serif;
    font-size: 8px;
    line-height: 12px;
    color: var(--ink-soft);
  }
  .contact-block::before {
    content: "";
    position: absolute;
    left: 0;
    top: 22px;
    width: 1px;
    height: 26px;
    background: var(--brand-orange);
  }
  .contact-phone {
    display: flex;
    align-items: center;
    gap: 4px;
  }
  .contact-phone svg { width: 7px; height: 7px; }
  .brand-name {
    position: absolute;
    top: 100px;
    left: 52px;
    display: flex;
    align-items: center;
    gap: 8px;
    font-size: 22px;
    font-weight: 400;
    color: var(--brand-orange);
  }
  .brand-mark {
    width: 10px;
    height: 10px;
    border-radius: 50%;
    background: var(--brand-orange);
  }
  .letter-meta {
    position: absolute;
    top: 188px;
    left: 100px;
    font-size: 10px;
    line-height: 13px;
  }
  .letter-meta p { margin: 0 0 12px; }
  .salutation {
    position: absolute;
    top: 316px;
    left: 100px;
    font-size: 12px;
    font-weight: 700;
  }
  .letter-body {
    position: absolute;
    top: 352px;
    left: 130px;
    width: 420px;
    font-size: 10px;
    line-height: 13px;
  }
  .letter-body p { margin: 0 0 14px; }
  .closing {
    position: absolute;
    top: 608px;
    left: 130px;
    font-size: 10px;
  }
  .signature {
    position: absolute;
    top: 640px;
    left: 170px;
    font-family: 'Satisfy', cursive;
    font-size: 30px;
    color: var(--ink);
  }
  .footer-swoosh {
    position: absolute;
    left: 0;
    bottom: 0;
    width: 600px;
    height: 110px;
  }
</style>
</head>
<body>
  <main class="letterhead">
    <address class="contact-block" style="font-style: normal;">
      2715 W. Pelican Lane<br>
      Englewood FL 34187<br>
      <span class="contact-phone">
        <svg viewBox="0 0 10 10" aria-hidden="true"><path d="M2 1 L4 1 L4.6 3.2 L3.4 4 Q4.3 5.8 6 6.6 L6.8 5.4 L9 6 L9 8 Q8.6 9 7.5 9 Q1 8.4 1 2.5 Q1 1.4 2 1 Z" fill="var(--brand-orange)"/></svg>
        941.382.6519
      </span>
    </address>

    <div class="brand-name"><span class="brand-mark"></span>Harbor Loom Floors</div>

    <section class="letter-meta">
      <p>January-03-2020</p>
      <p>Mr, Peter Vance<br>President</p>
      <p>Bridgeway Corporation<br>123 Street Name, Suite# 10<br>City, State, 120023</p>
    </section>

    <h2 class="salutation">Dear Mr, Peter</h2>

    <section class="letter-body">
      <p>Lorem ipsum dolor sit amet, consectetur adipiscing elit, sed do eiusmod tempor incididunt ut labore et dolore magna aliqua. Ut enim ad minim veniam, quis nostrud exercitation ullamco laboris nisi ut aliquip ex ea commodo consequat. Duis aute irure dolor in reprehenderit in voluptate velit esse cillum dolore eu fugiat nulla pariatur.</p>
      <p>Lorem ipsum dolor sit amet, consectetur adipiscing elit, sed do eiusmod tempor incididunt ut labore et dolore magna aliqua. Ut enim ad minim veniam, quis nostrud exercitation ullamco laboris nisi ut aliquip ex ea commodo consequat. Duis aute irure dolor in reprehenderit in voluptate velit esse cillum dolore eu fugiat nulla pariatur.</p>
      <p>Lorem ipsum dolor sit amet, consectetur adipiscing elit, sed do eiusmod tempor incididunt ut labore et dolore magna aliqua. Ut enim ad minim veniam, quis nostrud exercitation ullamco laboris nisi ut aliquip ex ea commodo consequat.</p>
      <p>Excepteur sint occaecat cupidatat non proident, sunt in culpa qui officia deserunt mollit anim id est laborum. re et dolore magnam aliquam quaerat voluptatem.</p>
    </section>

    <div class="closing">Regards</div>
    <div class="signature">Elena Marsh</div>

    <svg class="footer-swoosh" viewBox="0 0 600 110" preserveAspectRatio="none" aria-hidden="true">
      <path d="M0 58 Q300 -8 600 98 L600 101 Q300 2 0 66 Z" fill="var(--brand-grey)"/>
      <path d="M0 70 Q300 8 600 104 L600 110 L0 110 Z" fill="var(--brand-orange)"/>
    </svg>
  </main>
</body>
</html>
```